Corvana Tongue Works, LLC

We need a business card that includes information about our business and conveys a reliable business that provides document translation services and interpreters for a variety of corporate and individual clients. We want to come across as professional, reliable, yet approachable. It should include the following on one side:

ESL / ENL Language Classes, Private Lessons, and Online Tutors
PLEXA Training and Testing
Translating & Interpreting Services
Contact us about Over-the-Phone Interpreting in over 200 languages
24/7/365
www.corvanatongue.example

The other side should include (555) 481-3062

Rhoda Pelling, President
482 Garnet Ave., Ste. 219
Indianapolis, IN 40917

Please add USA as part of the address. Also, please add rmpelling@corvanatongueworks.example as the e-mail address. Thank you.

Target Market(s)

Business professionals, their families, the international community

Industry/Entity Type

Business

Contact Information for Business Card

24/7/365
www.corvanatongue.example

(555) 481-3062

Rhoda Pelling, President
482 Garnet Ave., Ste. 219
Indianapolis, IN 40917
USA

Font styles to use
Sans Serif

Colors

Designer to choose colors to be used in the design.

Requirements
Must have
• See project description
• e-mail address and web address
• Phone number
Nice to have
• a globe
• physical address
Should not have
• Should not have the same color scheme as other agencies in our market in Indiana unless it is blue and black. No purple or yellow.

```html
<!DOCTYPE html>
<html lang="en">
<head>
<meta charset="utf-8">
<title>Corvana Tongue Works, LLC – Business Card</title>
<link href="https://fonts.googleapis.com/css2?family=Open+Sans:wght@400;600;700&display=swap" rel="stylesheet">
<style>
  :root {
    --brand-blue: #2a92d3;
    --brand-blue-light: #3aa3e0;
    --ink: #1f1f1f;
    --muted: #3b3b3b;
    --paper: #ffffff;
    --stage: #e6e8eb;
  }
  * { box-sizing: border-box; margin: 0; padding: 0; }
  html, body { width: 1200px; height: 896px; overflow: hidden; }
  body {
    background: var(--stage);
    font-family: "Open Sans", Arial, sans-serif;
    display: flex;
    align-items: center;
    justify-content: center;
    gap: 50px;
  }
  .card {
    width: 525px;
    height: 300px;
    border-radius: 18px;
    box-shadow: 0 10px 30px rgba(0,0,0,0.18);
    position: relative;
    overflow: hidden;
  }

  /* Back side: services */
  .card-back {
    background: linear-gradient(160deg, var(--brand-blue-light), var(--brand-blue));
    color: var(--paper);
    display: flex;
    flex-direction: column;
    align-items: center;
    justify-content: center;
    padding: 0 30px;
  }
  .brand {
    display: flex;
    align-items: center;
    gap: 14px;
  }
  .brand-mark {
    width: 58px; height: 58px;
    border-radius: 50%;
    border: 3px solid currentColor;
    flex: none;
  }
  .brand-name {
    font-size: 24px;
    font-weight: 400;
    line-height: 1.05;
  }
  .card-back .rule {
    width: 400px;
    height: 1px;
    background: rgba(255,255,255,0.85);
    margin: 16px 0 12px;
    flex: none;
  }
  .services, .availability {
    list-style: none;
    text-align: center;
    font-size: 12.5px;
    font-weight: 600;
    line-height: 1.5;
  }

  /* Front side: contact */
  .card-front {
    background: var(--paper);
    display: flex;
    align-items: center;
    padding: 0 30px;
  }
  .card-front .brand {
    width: 200px;
    color: var(--brand-blue);
    flex: none;
  }
  .card-front .brand-name { color: var(--ink); font-size: 21px; }
  .divider {
    width: 1.5px;
    height: 150px;
    background: var(--brand-blue);
    margin: 0 20px 0 8px;
    flex: none;
  }
  .contact { color: var(--muted); font-size: 12.5px; line-height: 1.45; min-width: 0; }
  .contact .person {
    color: var(--brand-blue);
    font-size: 21px;
    font-weight: 600;
    text-transform: uppercase;
    letter-spacing: 0.3px;
    line-height: 1.1;
  }
  .contact .role { margin-bottom: 14px; }
  .contact .address { margin-bottom: 10px; }
  .contact .line { display: flex; align-items: center; gap: 6px; white-space: nowrap; }
  .contact .email { font-size: 11.5px; }
  .contact svg { width: 10px; height: 10px; flex: none; }
</style>
</head>
<body>

  <section class="card card-back" aria-label="Card back">
    <div class="brand">
      <span class="brand-mark"></span>
      <span class="brand-name">Corvana<br>Tongue Works, LLC</span>
    </div>
    <div class="rule"></div>
    <ul class="services">
      <li>ESL / ENL Language Classes, Private Lessons, and Online Tutors</li>
      <li>PLEXA Training and Testing</li>
      <li>Translating &amp; Interpreting Services</li>
    </ul>
    <div class="rule"></div>
    <ul class="availability">
      <li>Contact us about Over-the-Phone Interpreting in over 200 languages</li>
      <li>24/7/365</li>
      <li>www.corvanatongue.example</li>
    </ul>
  </section>

  <section class="card card-front" aria-label="Card front">
    <div class="brand">
      <span class="brand-mark"></span>
      <span class="brand-name">Corvana<br>Tongue<br>Works, LLC</span>
    </div>
    <div class="divider"></div>
    <div class="contact">
      <p class="person">Rhoda Pelling</p>
      <p class="role">President</p>
      <p class="address">482 Garnet Ave., Ste. 219<br>Indianapolis, IN 40917 USA</p>
      <p class="line">
        <svg viewBox="0 0 10 10" aria-hidden="true"><path d="M2 0.5 L4 2.8 L3 4 Q4.3 6 6 7 L7.2 6 L9.5 8 L8.2 9.5 Q3.5 9 0.5 1.8 Z" fill="#2a92d3"/></svg>
        (555) 481-3062
      </p>
      <p class="line email">
        <svg viewBox="0 0 10 10" aria-hidden="true"><rect x="0.5" y="2" width="9" height="6.5" fill="none" stroke="#2a92d3" stroke-width="1.2"/><path d="M0.5 2 L5 5.8 L9.5 2" fill="none" stroke="#2a92d3" stroke-width="1.2"/></svg>
        rmpelling@corvanatongueworks.example
      </p>
      <p class="line">
        <svg viewBox="0 0 10 10" aria-hidden="true"><circle cx="5" cy="5" r="4.3" fill="none" stroke="#2a92d3" stroke-width="1.1"/><ellipse cx="5" cy="5" rx="1.9" ry="4.3" fill="none" stroke="#2a92d3" stroke-width="0.9"/><path d="M0.7 5 H9.3" stroke="#2a92d3" stroke-width="0.9"/></svg>
        www.corvanatongue.example
      </p>
    </div>
  </section>

</body>
</html>
```